Veltrano.co - Polar Expeditions Specialists

We need a modern, visually striking business card for Veltrano.co, a company specialized in selling expedition cruises to the most remote regions on Earth, with a focus on the Arctic and Antarctica. The design should instantly communicate that the cardholder is an expert in polar travel. Use clean, premium aesthetics with cool tones like icy blue and white, possibly incorporating polar imagery (ice, glaciers, penguins, etc.)

Attached the logo

Contact Information for Business Card

Feels high-end and trustworthy.. Visually memorable — encourages people to keep it

Colors
0054AA
0677BA
7BADD7
CADEEF
E8F1F8

Requirements
Must have
• ice, glaciers, penguins, montains
Nice to have
• modern, transparente,

```html
<!DOCTYPE html>
<html lang="en">
<head>
<meta charset="utf-8">
<title>Veltrano.co – Business Card</title>
<link rel="stylesheet" href="https://fonts.googleapis.com/css2?family=Poppins:wght@400;600;800&display=swap">
<style>
  :root {
    --stage: #1c1c1c;
    --brand-blue: #3375b7;
    --paper: #ffffff;
    --ink-light: #ffffff;
  }
  * { margin: 0; padding: 0; box-sizing: border-box; }
  html, body { width: 1200px; height: 1015px; overflow: hidden; }
  body {
    background: var(--stage);
    font-family: "Poppins", sans-serif;
    display: flex;
    flex-direction: column;
    align-items: center;
    justify-content: center;
    gap: 56px;
  }
  .card {
    position: relative;
    width: 640px;
    height: 366px;
    overflow: hidden;
  }
  /* Front */
  .card-front {
    background: var(--brand-blue);
    display: flex;
    flex-direction: column;
    align-items: center;
    justify-content: center;
    color: var(--ink-light);
  }
  .brand-name {
    font-weight: 800;
    font-size: 66px;
    line-height: 1;
    letter-spacing: 0.5px;
  }
  .brand-tagline {
    font-weight: 600;
    font-size: 17px;
    margin-top: 8px;
    letter-spacing: 0.3px;
  }
  /* Back */
  .card-back { background: var(--paper); }
  .card-back .wave { position: absolute; inset: 0; width: 100%; height: 100%; }
  .holder {
    position: absolute;
    top: 20px;
    right: 36px;
    text-align: right;
    color: var(--brand-blue);
  }
  .holder-name { font-weight: 800; font-size: 31px; line-height: 1.1; }
  .holder-role { font-weight: 400; font-size: 17px; line-height: 1.3; }
  .back-brand {
    position: absolute;
    left: 40px;
    top: 138px;
    color: var(--brand-blue);
  }
  .back-brand .brand-name { font-size: 42px; }
  .back-brand .brand-tagline { font-size: 12.5px; margin-top: 6px; }
  .contact {
    position: absolute;
    right: 30px;
    top: 166px;
    list-style: none;
    color: var(--ink-light);
    font-size: 15px;
    line-height: 1.32;
    text-align: right;
  }
  .contact li { display: flex; justify-content: flex-end; align-items: flex-start; gap: 8px; }
  .contact .address { margin-top: 8px; }
  .contact svg { width: 15px; height: 15px; flex: none; margin-top: 3px; }
</style>
</head>
<body>
  <section class="card card-front">
    <div class="brand-name">Veltrano.co</div>
    <div class="brand-tagline">Polar Expeditions Specialists</div>
  </section>

  <section class="card card-back">
    <svg class="wave" viewBox="0 0 640 366" preserveAspectRatio="none" aria-hidden="true">
      <path d="M0,300 C180,325 260,260 330,190 C400,120 520,102 640,100 L640,366 L0,366 Z" fill="#3375b7"/>
      <path d="M0,314 C185,340 270,275 342,202 C410,134 525,116 640,114" fill="none" stroke="#ffffff" stroke-width="5"/>
      <path d="M0,286 C175,310 250,246 318,178 C390,106 515,90 640,88" fill="none" stroke="#3375b7" stroke-width="5"/>
    </svg>

    <div class="holder">
      <div class="holder-name">Marcus Hale</div>
      <div class="holder-role">Managing Director</div>
    </div>

    <div class="back-brand">
      <div class="brand-name">Veltrano.co</div>
      <div class="brand-tagline">Polar Expeditions Specialists</div>
    </div>

    <ul class="contact">
      <li>044-987 654 321
        <svg viewBox="0 0 24 24"><path fill="#fff" d="M6.6 10.8a15.1 15.1 0 0 0 6.6 6.6l2.2-2.2a1 1 0 0 1 1-.25 11.4 11.4 0 0 0 3.6.57 1 1 0 0 1 1 1V20a1 1 0 0 1-1 1A17 17 0 0 1 3 4a1 1 0 0 1 1-1h3.5a1 1 0 0 1 1 1c0 1.25.2 2.45.57 3.57a1 1 0 0 1-.25 1z"/></svg>
      </li>
      <li>hello@veltranomail.com
        <svg viewBox="0 0 24 24"><path fill="#fff" d="M2 5h20v14H2z"/><path d="M2 5l10 8 10-8" fill="none" stroke="#3375b7" stroke-width="2"/></svg>
      </li>
      <li>www.veltrano-polar.com
        <svg viewBox="0 0 24 24"><circle cx="12" cy="12" r="9.5" fill="none" stroke="#fff" stroke-width="2"/><path d="M2.5 12h19M12 2.5c3 3 3 16 0 19M12 2.5c-3 3-3 16 0 19" fill="none" stroke="#fff" stroke-width="1.6"/></svg>
      </li>
      <li class="address">18, Harbour Lane here<br>Nordland Bay, 80210
        <svg viewBox="0 0 24 24"><path fill="#fff" d="M12 2a7 7 0 0 0-7 7c0 5 7 13 7 13s7-8 7-13a7 7 0 0 0-7-7zm0 9.5A2.5 2.5 0 1 1 12 6.5a2.5 2.5 0 0 1 0 5z"/></svg>
      </li>
    </ul>
  </section>
</body>
</html>
```